UI Improvement for FlorKeep app

We are looking for a talented UI/UX designer to REFINE and enhance the visual design of our mobile application, FlorKeep. The app is fully functional, but we need a designer to improve its aesthetics by specifying design elements such as fonts, colors, spacing, and component styles.
Your task will be to analyze the CURRENT UI and provide detailed design specifications that will make the app more visually appealing, modern, and user-friendly.
TODO:
Review the existing FlorKeep app design (see attachments) and identify areas for visual improvement.
Provide a detailed UI style guide, including:
Typography (font choices, sizes, and weights)
Color palette (primary, secondary, and accent colors)
Component styling (buttons, forms, icons, and interactive elements)
Spacing and layout guidelines (margins, paddings, and alignment)
Ensure the design remains clean, modern, and professional while maintaining usability and accessibility.
Provide design mockups or visual examples (if possible) to illustrate the proposed changes.
Deliverables:
A UI Style Guide (PDF or Figma file) with specifications on fonts, colors, spacing, and UI components.
Optionally, before/after mockups or examples demonstrating the improvements.
Ideal Designer:
Strong experience in mobile UI/UX design.
Understanding of modern design trends and best practices.
Ability to communicate design choices clearly for easy developer implementation.
I have attached 7 images showcasing the main UI screens used in the FlorKeep app. These screens need visual enhancements to improve their overall look and user experience.
The images represent the current design in three key modes:
LIST Mode – Displays data in a structured list format.
READ Mode – Shows detailed information when a user selects an item.
ADD/EDIT Mode – Allows users to input or modify information.
Additionally, there is a ‘MORE’ page, which serves as a menu listing other features of the application.
Task Objective:
Please refine and improve these UIs to create a more modern, visually appealing, and user-friendly experience. Focus on typography, colors, spacing, and component styling to ensure a cohesive and polished design.
Look and feel
Each slider illustrates characteristics of the customer's brand and the style your logo design should communicate.

```html
<!DOCTYPE html>
<html lang="en">
<head>
<meta charset="utf-8">
<title>FlorKeep – More, Contacts, Contact</title>
<link href="https://fonts.googleapis.com/css2?family=Barlow:wght@400;500;600;700&display=swap" rel="stylesheet">
<style>
:root{
  --stage:#1c1c1c;
  --screen:#ffffff;
  --header:#e7f5fb;
  --title:#0b56a6;
  --nav:#0a4fa3;
  --nav-btn:#2a68b4;
  --accent:#0a98d8;
  --accent-soft:#d4edf8;
  --orange:#ff8a00;
  --green:#17b26a;
  --ink:#222;
  --muted:#555;
  --line:#e3eef4;
  --letter-bg:#f1f3f4;
}
*{box-sizing:border-box;margin:0;padding:0}
html,body{width:1200px;height:828px;overflow:hidden;background:var(--stage);font-family:"Barlow",sans-serif}
.canvas{position:relative;width:1200px;height:828px}
.phone{position:absolute;top:53px;width:334px;height:722px;background:var(--screen);border-radius:26px;overflow:hidden}
.phone--more{left:60px}.phone--contacts{left:434px}.phone--contact{left:807px}
.topbar{position:absolute;left:0;top:0;width:100%;height:48px;background:var(--header);display:flex;align-items:center;padding:0 26px}
.topbar h1{flex:1;text-align:center;font-size:14px;font-weight:700;color:var(--title);letter-spacing:.3px;margin-left:30px}
.topbar svg{width:11px;height:11px;fill:#444}
.topbar .tools{display:flex;gap:12px}
.box{position:absolute;left:28px;width:279px;background:#fff;border:1px solid var(--line);border-radius:6px}
.menu-item{height:37px;display:flex;align-items:center;padding-left:3px;font-size:11.5px;color:var(--muted)}
.menu-item .ico{width:32px;height:32px;border-radius:3px;background:var(--accent-soft);display:flex;align-items:center;justify-content:center;margin-right:18px}
.menu-item .ico svg{width:13px;height:13px;fill:var(--accent)}
.menu-item.is-active{border-color:transparent;box-shadow:0 2px 10px rgba(10,120,180,.08)}
.menu-item.is-active .ico{background:var(--accent)}
.menu-item.is-active .ico svg{fill:#fff}
.menu-item .tick{margin-left:auto;margin-right:18px;width:11px;height:11px}
.search{height:37px;display:flex;align-items:center;justify-content:space-between;padding:0 18px;font-size:11.5px;color:#555;border-color:transparent;box-shadow:0 2px 10px rgba(10,120,180,.07)}
.search svg{width:11px;height:11px;fill:#444}
.card{padding:12px 0 0 61px}
.card .letter{position:absolute;left:11px;top:12px;width:36px;height:36px;border-radius:5px;background:var(--letter-bg);font-weight:700;font-size:15px;color:#222;display:flex;align-items:center;justify-content:center}
.card h2{font-size:11.5px;font-weight:600;color:var(--ink);margin-bottom:5px}
.tags{display:grid;grid-template-columns:110px auto;row-gap:5px;font-size:11px}
.tag{display:flex;align-items:center;gap:6px}
.tag svg{width:10px;height:10px}
.tag--owner{color:var(--accent)}.tag--owner svg{fill:var(--accent)}
.tag--pilot{color:var(--orange)}.tag--pilot svg{fill:var(--orange)}
.tag--qual{color:var(--green)}.tag--qual svg{fill:var(--green)}
.tag--plain{color:var(--muted)}.tag--plain svg{fill:var(--muted)}
.add{height:37px;display:flex;align-items:center;padding-left:17px;font-size:11.5px;color:var(--muted);gap:12px}
.add svg{width:11px;height:11px;fill:#444}
.add.is-active{color:var(--accent);border-color:transparent;box-shadow:0 2px 10px rgba(10,120,180,.08)}
.add.is-active svg{fill:var(--accent)}
.group{border:none;border-radius:6px;color:#fff;padding:14px 17px 0;font-size:11.5px}
.group--pilots{background:var(--orange);height:65px}
.group--owner{background:var(--accent);height:97px}
.group .head{display:flex;justify-content:space-between;font-weight:600;margin-bottom:8px}
.group .head span:last-child{font-weight:400}
.group .row{display:flex;justify-content:space-between;line-height:18px}
.group .row svg{width:10px;height:10px;fill:#fff;margin-top:4px;flex:none}
.tabbar{position:absolute;left:0;bottom:0;width:100%;height:60px;background:var(--nav)}
.tab{position:absolute;top:13px;width:34px;height:34px;border-radius:50%;background:var(--nav-btn);display:flex;align-items:center;justify-content:center}
.tab svg{width:13px;height:13px;fill:#fff}
.tab.is-active{background:#fff}.tab.is-active svg{fill:var(--nav)}
.t1{left:31px}.t2{left:90px}.t3{left:150px}.t4{left:209px}.t5{left:269px}
</style>
</head>
<body>
<svg width="0" height="0" style="position:absolute">
  <symbol id="i-back" viewBox="0 0 16 16"><path d="M11 2 5 8l6 6-1.6 1.6L1.8 8 9.4.4z"/></symbol>
  <symbol id="i-search" viewBox="0 0 16 16"><path d="M6.5 0a6.5 6.5 0 0 1 5.2 10.4l4.3 4.3-1.4 1.4-4.3-4.3A6.5 6.5 0 1 1 6.5 0zm0 2a4.5 4.5 0 1 0 0 9 4.5 4.5 0 0 0 0-9z"/></symbol>
  <symbol id="i-bell" viewBox="0 0 16 16"><path d="M8 0a1.3 1.3 0 0 1 1.3 1.4A5 5 0 0 1 13 6.4V10l2 2.5H1L3 10V6.4a5 5 0 0 1 3.7-5A1.3 1.3 0 0 1 8 0zM6 13.5h4a2 2 0 0 1-4 0z"/></symbol>
  <symbol id="i-plane" viewBox="0 0 16 16"><path d="M15 1c.8.8-.2 2.6-1.5 3.9L11.3 7l1.8 7-1.4 1.4-3.1-5.7-2.4 2.3.4 2.6-1.2 1.2-1.4-3-3-1.4 1.2-1.2 2.6.4 2.3-2.4L1.4 5.1 2.8 3.7l7 1.8 2.2-2.2C13.3 2 14.2.2 15 1z"/></symbol>
  <symbol id="i-lock" viewBox="0 0 16 16"><path d="M8 0a4 4 0 0 1 4 4H10a2 2 0 0 0-4 0v3h8v9H2V7h2V4a4 4 0 0 1 4-4z"/></symbol>
  <symbol id="i-user" viewBox="0 0 16 16"><circle cx="8" cy="4.5" r="4"/><path d="M1 16c0-4 3-6.5 7-6.5s7 2.5 7 6.5z"/></symbol>
  <symbol id="i-cal" viewBox="0 0 16 16"><path d="M3 0h2v2h6V0h2v2h3v14H0V2h3zM2 6v8h12V6zm1 1h2v2H3zm4 0h2v2H7zm4 0h2v2h-2zM3 11h2v2H3zm4 0h2v2H7zm4 0h2v2h-2z"/></symbol>
  <symbol id="i-users" viewBox="0 0 16 16"><circle cx="8" cy="4" r="3"/><circle cx="3" cy="5" r="2.2"/><circle cx="13" cy="5" r="2.2"/><path d="M3 14c0-3 2.2-5 5-5s5 2 5 5zM0 13c0-2 1.2-3.6 3-3.6.6 0 1 .1 1.4.3A6 6 0 0 0 2.5 13zm16 0h-2.5a6 6 0 0 0-1.9-3.3c.4-.2.8-.3 1.4-.3 1.8 0 3 1.6 3 3.6z"/></symbol>
  <symbol id="i-gauge" viewBox="0 0 16 16"><path d="M8 2a8 8 0 0 1 8 8c0 1.5-.4 2.9-1.1 4H1.1A8 8 0 0 1 8 2zm-5 7a1 1 0 1 0 0 2 1 1 0 0 0 0-2zm2-3.5a1 1 0 1 0 0 2 1 1 0 0 0 0-2zM13 9a1 1 0 1 0 0 2 1 1 0 0 0 0-2zm-1.3-3.2L8.7 9A1.5 1.5 0 1 0 9.5 10l3.3-3.4z"/></symbol>
  <symbol id="i-pin" viewBox="0 0 16 16"><path d="M8 0a5.5 5.5 0 0 1 5.5 5.5C13.5 10 8 16 8 16S2.5 10 2.5 5.5A5.5 5.5 0 0 1 8 0zm0 3.3a2.2 2.2 0 1 0 0 4.4 2.2 2.2 0 0 0 0-4.4z"/></symbol>
  <symbol id="i-gift" viewBox="0 0 16 16"><path d="M1 5h14v3H1zm1 4h5v7H2zm7 0h5v7H9zM8 4.5C6 4.5 3.5 4 4 2s3 .5 4 2.5zm0 0c1-2 3.5-4.5 4-2.5s-2 2.5-4 2.5z"/></symbol>
  <symbol id="i-pencil" viewBox="0 0 16 16"><path d="m11.5 1 3.5 3.5L5 14.5H1.5V11zM0 16h16"/></symbol>
  <symbol id="i-gear" viewBox="0 0 16 16"><path d="M7 0h2l.4 2.2 1.5.6 1.8-1.3 1.4 1.4-1.3 1.8.6 1.5L16 7v2l-2.2.4-.6 1.5 1.3 1.8-1.4 1.4-1.8-1.3-1.5.6L9 16H7l-.4-2.2-1.5-.6-1.8 1.3-1.4-1.4 1.3-1.8-.6-1.5L0 9V7l2.2-.4.6-1.5-1.3-1.8 1.4-1.4 1.8 1.3 1.5-.6zm1 5a3 3 0 1 0 0 6 3 3 0 0 0 0-6z"/></symbol>
  <symbol id="i-check" viewBox="0 0 16 16"><path d="M2 8.2 3.6 6.6l3 3L12.5 3.7 14 5.3l-7.4 7.4z"/></symbol>
  <symbol id="i-checkc" viewBox="0 0 16 16"><path fill="#0a98d8" d="M8 0a8 8 0 1 1 0 16A8 8 0 0 1 8 0z"/><path fill="#fff" d="m4 8.2 1.2-1.2 2 2 3.7-3.7L12 6.5l-4.8 4.8z"/></symbol>
  <symbol id="i-plus" viewBox="0 0 16 16"><path d="M8 0a8 8 0 1 1 0 16A8 8 0 0 1 8 0zM7 4v3H4v2h3v3h2V9h3V7H9V4z"/></symbol>
  <symbol id="i-down" viewBox="0 0 16 16"><path d="M2 5 3.6 3.4 8 7.8l4.4-4.4L14 5l-6 6z"/></symbol>
  <symbol id="i-pilot" viewBox="0 0 16 16"><path d="M3 2.5 8 0l5 2.5-1 1.5H4zM4.5 5h7a3.5 3.5 0 0 1-7 0zM2 16c0-3.5 2.5-6 6-6s6 2.5 6 6zm5-5 1 3 1-3z"/></symbol>
  <symbol id="i-hand" viewBox="0 0 16 16"><path d="M5 1.5a1.3 1.3 0 0 1 2.6 0V7l.4-.1V5.8a1.2 1.2 0 0 1 2.4 0v1.6a1.2 1.2 0 0 1 2.3.3v.6a1.1 1.1 0 0 1 2.2.4v3.3C14.9 14 13.2 16 10.8 16H8.6c-1.6 0-2.7-.8-3.6-2L1.6 9.8a1.3 1.3 0 0 1 2-1.7L5 9.5z"/></symbol>
  <symbol id="i-grid" viewBox="0 0 16 16"><rect x="0" y="0" width="7" height="7" rx="1"/><rect x="9" y="0" width="7" height="7" rx="1"/><rect x="0" y="9" width="7" height="7" rx="1"/><path d="m12.5 8.8 3.7 3.7-3.7 3.7-3.7-3.7z"/></symbol>
</svg>

<main class="canvas">

  <!-- More menu -->
  <section class="phone phone--more">
    <header class="topbar">
      <svg><use href="#i-back"/></svg><h1>MORE</h1>
      <div class="tools"><svg><use href="#i-search"/></svg><svg><use href="#i-bell"/></svg></div>
    </header>
    <div class="box menu-item is-active" style="top:73px"><span class="ico"><svg><use href="#i-plane"/></svg></span>Flight<svg class="tick"><use href="#i-checkc"/></svg></div>
    <div class="box menu-item" style="top:125px"><span class="ico"><svg><use href="#i-lock"/></svg></span>Login</div>
    <div class="box menu-item" style="top:176px"><span class="ico"><svg><use href="#i-user"/></svg></span>Account</div>
    <div class="box menu-item" style="top:228px"><span class="ico"><svg><use href="#i-cal"/></svg></span>Calendar</div>
    <div class="box menu-item" style="top:279px"><span class="ico"><svg><use href="#i-users"/></svg></span>Users</div>
    <div class="box menu-item" style="top:331px"><span class="ico"><svg><use href="#i-gauge"/></svg></span>Dashboard</div>
    <div class="box menu-item" style="top:382px"><span class="ico"><svg><use href="#i-pin"/></svg></span>Tracking</div>
    <div class="box menu-item" style="top:434px"><span class="ico"><svg><use href="#i-gift"/></svg></span>Outreach Event</div>
    <div class="box menu-item" style="top:485px"><span class="ico"><svg><use href="#i-pencil"/></svg></span>Maintenance Resource</div>
    <div class="box menu-item" style="top:537px"><span class="ico"><svg><use href="#i-gear"/></svg></span>Settings</div>
    <nav class="tabbar">
      <span class="tab t1"><svg><use href="#i-user"/></svg></span><span class="tab t2"><svg><use href="#i-pilot"/></svg></span>
      <span class="tab t3"><svg><use href="#i-plane"/></svg></span><span class="tab t4"><svg><use href="#i-hand"/></svg></span>
      <span class="tab t5 is-active"><svg><use href="#i-grid"/></svg></span>
    </nav>
  </section>

  <!-- Contacts list -->
  <section class="phone phone--contacts">
    <header class="topbar">
      <svg><use href="#i-back"/></svg><h1>CONTACTS</h1>
      <div class="tools"><svg><use href="#i-search"/></svg><svg><use href="#i-bell"/></svg></div>
    </header>
    <div class="box search" style="top:73px">Search<svg><use href="#i-search"/></svg></div>
    <article class="box card" style="top:127px;height:77px"><span class="letter">A</span><h2>Alder, Corin</h2>
      <div class="tags"><span class="tag tag--owner"><svg><use href="#i-check"/></svg>Aircraft Owner</span><span class="tag tag--plain"><svg><use href="#i-check"/></svg>Enthusiast-e</span><span class="tag tag--plain"><svg><use href="#i-check"/></svg>Flight Support</span></div></article>
    <article class="box card" style="top:221px;height:77px"><span class="letter">A</span><h2>Ashby, Marcus, Reid</h2>
      <div class="tags"><span class="tag tag--owner"><svg><use href="#i-check"/></svg>Aircraft Owner</span><span class="tag tag--pilot"><svg><use href="#i-check"/></svg>Pilot</span><span class="tag tag--qual"><svg><use href="#i-check"/></svg>Qualified Pilot</span></div></article>
    <article class="box card" style="top:314px;height:77px"><span class="letter">B</span><h2>Bellamy, Rowan</h2>
      <div class="tags"><span class="tag tag--owner"><svg><use href="#i-check"/></svg>Aircraft Owner</span><span class="tag tag--pilot"><svg><use href="#i-check"/></svg>Pilot</span><span class="tag tag--qual"><svg><use href="#i-check"/></svg>Qualified Pilot</span></div></article>
    <article class="box card" style="top:409px;height:77px"><span class="letter">B</span><h2>Brandt, Elias</h2>
      <div class="tags"><span class="tag tag--owner"><svg><use href="#i-check"/></svg>Aircraft Owner</span><span class="tag tag--pilot"><svg><use href="#i-check"/></svg>Pilot</span><span class="tag tag--qual"><svg><use href="#i-check"/></svg>Qualified Pilot</span></div></article>
    <article class="box card" style="top:501px;height:60px"><span class="letter">C</span><h2>Castel, Ivy, Noor</h2>
      <div class="tags"><span class="tag tag--pilot"><svg><use href="#i-check"/></svg>Pilot</span></div></article>
    <article class="box card" style="top:577px;height:60px"><span class="letter">C</span><h2>Cortez Alvaro, Hugo, Marisel</h2>
      <div class="tags"><span class="tag tag--pilot"><svg><use href="#i-check"/></svg>Pilot</span></div></article>
    <nav class="tabbar">
      <span class="tab t1 is-active"><svg><use href="#i-user"/></svg></span><span class="tab t2"><svg><use href="#i-pilot"/></svg></span>
      <span class="tab t3"><svg><use href="#i-plane"/></svg></span><span class="tab t4"><svg><use href="#i-hand"/></svg></span>
      <span class="tab t5"><svg><use href="#i-grid"/></svg></span>
    </nav>
  </section>

  <!-- Contact edit -->
  <section class="phone phone--contact">
    <header class="topbar">
      <svg><use href="#i-back"/></svg><h1>CONTACT</h1>
      <div class="tools"><svg><use href="#i-search"/></svg><svg><use href="#i-bell"/></svg></div>
    </header>
    <div class="box search" style="top:73px">Search<svg><use href="#i-search"/></svg></div>
    <div class="box add is-active" style="top:127px"><svg><use href="#i-plus"/></svg>Add Email -e</div>
    <div class="box add" style="top:173px"><svg><use href="#i-plus"/></svg>Add Social Media -e</div>
    <div class="box add" style="top:218px"><svg><use href="#i-plus"/></svg>Add Emergency Contact -e</div>
    <div class="box add" style="top:264px"><svg><use href="#i-plus"/></svg>Add Personal Information -e</div>
    <div class="box add" style="top:310px"><svg><use href="#i-plus"/></svg>Add Work Info -e</div>
    <div class="box add" style="top:355px"><svg><use href="#i-plus"/></svg>Add Skills/Talents -e</div>
    <div class="box add" style="top:401px"><svg><use href="#i-plus"/></svg>Add Resources -e</div>
    <div class="box group group--pilots" style="top:451px">
      <div class="head"><span>Pilots -e</span><span>Collapse</span></div>
      <div class="row"><span>Alder, Corin, 5208113, 04/12/24</span><svg><use href="#i-down"/></svg></div>
    </div>
    <div class="box group group--owner" style="top:529px">
      <div class="head"><span>Aircraft Owner -e</span><span>Collapse</span></div>
      <div class="row"><span>Personal: Alder, Corin: Aerolux:<br>47K: Aerolux<br>Aircraft Company, Beacon Motor, 2400</span><svg><use href="#i-down"/></svg></div>
    </div>
    <nav class="tabbar">
      <span class="tab t1 is-active"><svg><use href="#i-user"/></svg></span><span class="tab t2"><svg><use href="#i-pilot"/></svg></span>
      <span class="tab t3"><svg><use href="#i-plane"/></svg></span><span class="tab t4"><svg><use href="#i-hand"/></svg></span>
      <span class="tab t5"><svg><use href="#i-grid"/></svg></span>
    </nav>
  </section>

</main>
</body>
</html>
```